Dental Medical History Form - Content provided

Design a medical history form for a dental practice. Content is provided so all that is needed is the formatting to make it look great and easy to read.

"Patient Information" to include all information contained in top portion of the "Patient Medical History Form" docx file.

"Medical History" should follow the formatting and content of the "Exact Medical History" file as this is what the entry fields look like in our practice software and so we would like it to match.

1st page - Patient info, allergies, medications, antibiotics, joint replacement, pregnancy.

2nd page - Do you have, or have you had, any of the following? . . . . . . .
Updates

Target Market(s)

All ages but must be clear enough for elderly to read. Use as much space as possible to keep font size bigger yet keep to two pages

Industry/Entity Type

Dental

Font styles to use
Sans Serif

Requirements
Must have
• All content provided
• Our logo at the top (file provided)
• Century Gothic Font
• Limit to two pages

```html
<!DOCTYPE html>
<html lang="en">
<head>
<meta charset="utf-8">
<title>Confidential Medical History</title>
<link href="https://fonts.googleapis.com/css2?family=Questrial&display=swap" rel="stylesheet">
<style>
  :root {
    --ink: #3d3d42;
    --ink-dark: #333337;
    --rule: #2f2f33;
    --frame: #bdbdbd;
    --band: #4d4d52;
    --footer: #5b5b60;
    --paper: #ffffff;
  }
  * { box-sizing: border-box; margin: 0; padding: 0; }
  html, body { width: 848px; height: 1200px; overflow: hidden; background: var(--paper); }
  body { font-family: "Questrial", "Century Gothic", sans-serif; color: var(--ink); font-size: 13px; }
  .page { position: relative; width: 848px; height: 1200px; }

  .brand { position: absolute; left: 52px; top: 78px; display: flex; align-items: center; gap: 12px; color: var(--ink-dark); font-size: 30px; line-height: 1; white-space: nowrap; }
  .brand-mark { width: 14px; height: 14px; border-radius: 50%; background: var(--band); }

  .contact { position: absolute; left: 612px; top: 55px; font-size: 12.5px; color: var(--ink-dark); line-height: 16px; font-weight: bold; }
  .contact p.gap { margin-top: 4px; }

  .header-band { position: absolute; left: 0; top: 146px; width: 298px; height: 8px; background: var(--band); clip-path: polygon(0 0, 290px 0, 298px 8px, 0 8px); }
  .header-rule { position: absolute; left: 0; top: 153px; width: 802px; border-top: 1.5px solid var(--band); }

  .title { position: absolute; top: 178px; left: 0; width: 848px; text-align: center; font-size: 20px; font-weight: bold; color: var(--ink-dark); letter-spacing: 0.2px; }

  .panel { position: absolute; left: 46px; width: 756px; border: 1px solid var(--frame); }

  .field { position: absolute; display: flex; align-items: flex-end; height: 16px; white-space: nowrap; }
  .field .line { flex: 1; border-bottom: 1px solid var(--rule); margin-left: 1px; height: 13px; }
  .label { position: absolute; white-space: nowrap; height: 16px; line-height: 16px; }

  .options { position: absolute; display: flex; align-items: center; white-space: nowrap; }
  .opt { display: flex; align-items: center; }
  .dot { display: inline-block; width: 20px; height: 20px; border: 1.3px solid var(--ink-dark); border-radius: 50%; margin-left: 2px; }

  .tick { display: inline-block; width: 23px; height: 23px; vertical-align: middle; margin: 0 6px 0 8px; }

  .write-line { position: absolute; border-bottom: 1px solid var(--rule); }

  .footer { position: absolute; left: 0; top: 1102px; width: 848px; height: 98px; background: var(--footer); }
  .footer-note { position: absolute; right: 58px; top: 17px; color: #fff; font-style: italic; font-weight: bold; font-size: 13px; }
</style>
</head>
<body>
<div class="page">

  <header>
    <div class="brand">
      <span class="brand-mark"></span>
      <span class="brand-name">Harbourline Dental</span>
    </div>
    <div class="contact">
      <p>Suite 4/18 Coastal Parade</p>
      <p>Seaview NSW 2299</p>
      <p class="gap">(02) 4000 1234</p>
      <p class="gap">www.harbourlinedental.com.au</p>
    </div>
    <div class="header-band"></div>
    <div class="header-rule"></div>
  </header>

  <h1 class="title">CONFIDENTIAL MEDICAL HISTORY</h1>

  <!-- Patient details -->
  <section class="panel" style="top:222px;height:287px;"></section>
  <div class="field" style="left:62px;top:229px;width:332px;">Name:<span class="line"></span></div>
  <div class="label" style="left:62px;top:249px;">Title</div>
  <div class="label" style="left:148px;top:249px;">First</div>
  <div class="label" style="left:222px;top:249px;">Middle</div>
  <div class="label" style="left:320px;top:249px;">Last</div>
  <div class="field" style="left:62px;top:280px;width:332px;">Address:<span class="line"></span></div>
  <div class="field" style="left:62px;top:300px;width:332px;">DOB:<span class="line"></span></div>
  <div class="field" style="left:62px;top:320px;width:332px;">Email Address:<span class="line"></span></div>
  <div class="label" style="left:62px;top:340px;">Phone Numbers:</div>
  <div class="field" style="left:86px;top:360px;width:308px;"><span style="width:49px">Mobile:</span><span class="line"></span></div>
  <div class="field" style="left:86px;top:380px;width:308px;"><span style="width:49px">Home:</span><span class="line"></span></div>
  <div class="field" style="left:86px;top:400px;width:308px;"><span style="width:49px">Work:</span><span class="line"></span></div>
  <div class="label" style="left:62px;top:420px;">Emergency Contact Person:</div>
  <div class="field" style="left:62px;top:440px;width:332px;">Name:<span class="line"></span></div>
  <div class="field" style="left:62px;top:460px;width:332px;">Relationship:<span class="line"></span></div>
  <div class="field" style="left:62px;top:480px;width:332px;">Phone number:<span class="line"></span></div>

  <div class="label" style="left:418px;top:229px;">General Practitioner:</div>
  <div class="field" style="left:418px;top:249px;width:370px;">Name:<span class="line"></span></div>
  <div class="field" style="left:418px;top:269px;width:370px;">Practice Name:<span class="line"></span></div>
  <div class="field" style="left:418px;top:289px;width:370px;">Phone Number:<span class="line"></span></div>
  <div class="label" style="left:418px;top:329px;">Do you have a health fund with dental cover?&nbsp; Yes&nbsp; or No</div>
  <div class="field" style="left:418px;top:349px;width:370px;">If so, what is the name of the fund?<span class="line"></span></div>
  <div class="field" style="left:418px;top:369px;width:370px;">Fund Number?<span class="line"></span></div>
  <div class="label" style="left:418px;top:389px;">Priority Number on card: 0&nbsp; 1&nbsp; 2&nbsp; 3&nbsp; 4&nbsp;&nbsp; 5</div>
  <div class="field" style="left:418px;top:429px;width:370px;">Occupation:<span class="line"></span></div>
  <div class="field" style="left:418px;top:449px;width:370px;">Referrred by:<span class="line"></span></div>

  <!-- Allergies -->
  <section class="panel" style="top:529px;height:114px;"></section>
  <div class="label" style="left:62px;top:536px;">Please indicate if&nbsp; youare allergic to any of the following<svg class="tick" viewBox="0 0 24 24" aria-hidden="true"><circle cx="12" cy="12" r="12" fill="#4d4d52"/><path d="M6.5 12.5l3.6 3.6 7.4-7.6" fill="none" stroke="#fff" stroke-width="2.4" stroke-linecap="round" stroke-linejoin="round"/></svg>?</div>
  <div class="options" style="left:62px;top:572px;width:714px;justify-content:space-between;">
    <span class="opt">Aspirin<span class="dot"></span></span>
    <span class="opt">Codeine<span class="dot"></span></span>
    <span class="opt">Penicillin<span class="dot"></span></span>
    <span class="opt">Sulfites<span class="dot"></span></span>
    <span class="opt">Latex<span class="dot"></span></span>
    <span class="opt">Local Anaesthetic<span class="dot"></span></span>
    <span class="opt">Lactose<span class="dot"></span></span>
    <span class="opt">Nickel<span class="dot"></span></span>
  </div>
  <div class="field" style="left:62px;top:607px;width:726px;">Other:<span class="line"></span></div>

  <!-- Medication -->
  <section class="panel" style="top:663px;height:115px;"></section>
  <div class="label" style="left:62px;top:671px;">Are you currently taking, or have ever taken, any of the following medication<svg class="tick" viewBox="0 0 24 24" aria-hidden="true"><circle cx="12" cy="12" r="12" fill="#4d4d52"/><path d="M6.5 12.5l3.6 3.6 7.4-7.6" fill="none" stroke="#fff" stroke-width="2.4" stroke-linecap="round" stroke-linejoin="round"/></svg>?</div>
  <div class="options" style="left:62px;top:706px;width:615px;justify-content:space-between;">
    <span class="opt">Asthma inhaler<span class="dot"></span></span>
    <span class="opt">Anti-epileptics<span class="dot"></span></span>
    <span class="opt">Anti-depressants<span class="dot"></span></span>
    <span class="opt">Blood Pressure<span class="dot"></span></span>
    <span class="opt">Blood Thinners<span class="dot"></span></span>
  </div>
  <div class="options" style="left:62px;top:740px;width:709px;justify-content:space-between;">
    <span class="opt">Bisphosphonates<span class="dot"></span></span>
    <span class="opt">Chemotherapy<span class="dot"></span></span>
    <span class="opt">Insulin<span class="dot"></span></span>
    <span class="opt">Immunosuppressants<span class="dot"></span></span>
    <span class="opt">Steroids<span class="dot"></span></span>
    <span class="opt">Oral Contraceptive<span class="dot"></span></span>
  </div>

  <!-- Medication details -->
  <section class="panel" style="top:798px;height:109px;"></section>
  <div class="label" style="left:62px;top:806px;">Please specify medication name, dose, and frequency where possible:</div>
  <div class="write-line" style="left:62px;top:843px;width:221px;"></div>
  <div class="write-line" style="left:62px;top:863px;width:221px;"></div>
  <div class="write-line" style="left:62px;top:883px;width:221px;"></div>
  <div class="write-line" style="left:308px;top:843px;width:222px;"></div>
  <div class="write-line" style="left:308px;top:863px;width:222px;"></div>
  <div class="write-line" style="left:308px;top:883px;width:222px;"></div>
  <div class="write-line" style="left:554px;top:843px;width:221px;"></div>
  <div class="write-line" style="left:554px;top:863px;width:221px;"></div>
  <div class="write-line" style="left:554px;top:883px;width:221px;"></div>

  <!-- Further questions -->
  <section class="panel" style="top:927px;height:151px;"></section>
  <div class="options" style="left:62px;top:937px;">
    <span class="opt">Do you require antibiotic cover? Yes<span class="dot"></span></span>
    <span class="opt" style="margin-left:22px;">No<span class="dot"></span></span>
  </div>
  <div class="options" style="left:62px;top:976px;">
    <span class="opt">Have you had a joint replacement? Yes<span class="dot"></span></span>
    <span class="opt" style="margin-left:22px;">No<span class="dot"></span></span>
  </div>
  <div class="label" style="left:62px;top:1016px;">Women:</div>
  <div class="options" style="left:62px;top:1036px;">
    <span class="opt">Are you pregnant? Yes<span class="dot"></span></span>
    <span class="opt" style="margin-left:22px;">No<span class="dot"></span></span>
    <span class="opt" style="margin-left:36px;">Possible or Breast Feeding? Yes<span class="dot"></span></span>
    <span class="opt" style="margin-left:18px;">No<span class="dot"></span></span>
  </div>

  <footer class="footer">
    <p class="footer-note">Please Turnover</p>
  </footer>
</div>
</body>
</html>
```